Coastal Learner Bureau business cards

Australian company about to start offering its services. We recruit international students to come to study English, vocational education and postgraduate courses in Australia. We help them find the institution and select the right city they want to come to Australia. We are a young, online oriented and supportive agency. Our clients are between 18 and 35 years old, mainly University students, young professionals or people with work experience. We provide much more information that any other agency offer. We administrate a Facebook group with more than 11.000 members that daily ask questions about general information when coming to Australia, while they are here and even after they leave the country

Target Market(s)

International students from South America, Central America and Europe

Industry/Entity Type

Student

Contact Information for Business Card

Tomas Bilbrea
Managing Director
tomas@kelvarin.com.au
www.kelvoria.com.au
+61 491058264
Melbourne, Australia

Font styles to use
Serif
Sans Serif

Colors

Designer to choose colors to be used in the design.

Requirements
Must have
• Horizontal design
• Standard business card size and shape. If font uses green or yellow colours, they will have to match the ones from the logo
Nice to have
• UPDATE: Use the contents of the green image to design one of the card sides. Use our logo in the background of that side as watermark.
• Passport image, or immigration stamps. A picture of the Yarra River (from Melbourne) would be cool as well.
Should not have
• Non-standard business card size and shape
• Not black as the background colour of any sides as we are not a VIP agency or a hight class service. We are orientes to young people and they like colours, pictures, something attractive.
• Vertical design
• NO YELLOW or BLACK AS THE BACKGROUND COLOUR OF ANY SIDE OF THE BIZ CARD

```html
<!DOCTYPE html>
<html lang="en">
<head>
<meta charset="utf-8">
<title>Coastal Learner Bureau business cards</title>
<link rel="stylesheet" href="https://fonts.googleapis.com/css2?family=Open+Sans:wght@400;600;700&display=swap">
<style>
  :root {
    --page-bg: #e9e9e7;
    --gold-line: #d8b21a;
    --green: #1f6b3a;
    --green-light: #2a8049;
    --green-dark: #175a30;
    --paper: #f4f4f2;
    --white: #ffffff;
    --ink-green: #1f6b3a;
  }
  * { margin: 0; padding: 0; box-sizing: border-box; }
  html, body {
    width: 1200px; height: 900px; overflow: hidden;
    background: var(--page-bg);
    font-family: "Open Sans", Arial, sans-serif;
  }
  .sheet { position: relative; width: 1200px; height: 900px; }
  .card {
    position: absolute; left: 270px;
    width: 660px; height: 377px;
    overflow: hidden;
    box-shadow: 0 6px 18px rgba(0,0,0,0.18);
  }
  .card--front {
    top: 52px;
    background: linear-gradient(115deg, var(--green-light) 0%, var(--green) 50%, var(--green-dark) 100%);
  }
  .card--front-accent {
    position: absolute; left: 0; right: 0; bottom: 0; height: 8px;
    background: var(--gold-line);
  }
  .card--back { top: 471px; background: var(--paper); }

  .brand-name {
    position: absolute;
    font-weight: 700;
    letter-spacing: 1px;
    line-height: 1;
  }
  .card--front .brand-name {
    left: 0; right: 0; top: 130px;
    text-align: center; font-size: 64px; color: var(--white);
  }
  .tagline {
    position: absolute; left: 0; right: 0; top: 270px;
    display: flex; align-items: center; justify-content: center; gap: 14px;
    color: var(--white); font-size: 15px; font-weight: 600;
  }
  .tagline::before, .tagline::after {
    content: ""; width: 200px; height: 1px; background: rgba(255,255,255,0.8);
  }

  .card-wave { position: absolute; inset: 0; width: 100%; height: 100%; }
  .card--back .brand-name {
    left: 60px; top: 140px; font-size: 54px; color: var(--ink-green);
  }
  .contact-list {
    position: absolute; right: 30px; top: 178px;
    list-style: none; color: var(--white); font-size: 14px;
    text-align: right;
  }
  .contact-list li {
    display: flex; align-items: center; justify-content: flex-end; gap: 9px;
    height: 24px;
  }
  .contact-icon { width: 14px; height: 14px; flex: none; }
  .person {
    position: absolute; left: 60px; bottom: 34px; color: var(--white);
  }
  .person-name { font-size: 19px; font-weight: 700; letter-spacing: 0.5px; text-transform: uppercase; }
  .person-title { font-size: 17px; font-weight: 400; letter-spacing: 0.5px; text-transform: uppercase; }
</style>
</head>
<body>
<main class="sheet">

  <section class="card card--front" aria-label="Card front">
    <div class="brand-name">Kelvoria</div>
    <p class="tagline">Hacemos más por ti!</p>
    <div class="card--front-accent"></div>
  </section>

  <section class="card card--back" aria-label="Card back">
    <svg class="card-wave" viewBox="0 0 660 377" preserveAspectRatio="none" aria-hidden="true">
      <path d="M0,262 C150,330 260,305 340,215 C400,148 520,100 660,88 L660,377 L0,377 Z" fill="var(--green)"/>
      <path d="M0,248 C150,316 260,291 340,201 C400,134 520,86 660,74" fill="none" stroke="var(--gold-line)" stroke-width="5"/>
    </svg>

    <div class="brand-name">Kelvoria</div>

    <ul class="contact-list">
      <li>Melbourne, Australia
        <svg class="contact-icon" viewBox="0 0 14 14" aria-hidden="true"><path d="M7 1a4 4 0 0 1 4 4c0 3-4 8-4 8S3 8 3 5a4 4 0 0 1 4-4z" fill="#fff"/><circle cx="7" cy="5" r="1.5" fill="var(--green)"/></svg>
      </li>
      <li>+61 491058264
        <svg class="contact-icon" viewBox="0 0 14 14" aria-hidden="true"><path d="M3 1l2.5 0 1 3-1.5 1.2a7 7 0 0 0 3.8 3.8L10 7.5l3 1V11a2 2 0 0 1-2 2C5.5 13 1 8.5 1 3a2 2 0 0 1 2-2z" fill="#fff"/></svg>
      </li>
      <li>tomas@kelvarin.com.au
        <svg class="contact-icon" viewBox="0 0 14 14" aria-hidden="true"><rect x="1" y="3" width="12" height="8" rx="1" fill="#fff"/><path d="M1.5 3.5L7 8l5.5-4.5" fill="none" stroke="var(--green)" stroke-width="1.2"/></svg>
      </li>
      <li>www.kelvoria.com.au
        <svg class="contact-icon" viewBox="0 0 14 14" aria-hidden="true"><circle cx="7" cy="7" r="6" fill="#fff"/><ellipse cx="7" cy="7" rx="2.5" ry="6" fill="none" stroke="var(--green)" stroke-width="1"/><path d="M1 7h12" stroke="var(--green)" stroke-width="1"/></svg>
      </li>
    </ul>

    <div class="person">
      <p class="person-name">Tomas Bilbrea</p>
      <p class="person-title">Managing Director</p>
    </div>
  </section>

</main>
</body>
</html>
```